Tall Fern Roofing Business Card

Need a business card with the logo that was designed here

Contact Information for Business Card

Name, Title, Phone, Email, Website, Company name

```html
<!DOCTYPE html>
<html lang="en">
<head>
<meta charset="utf-8">
<title>Tall Fern Roofing Business Card</title>
<link href="https://fonts.googleapis.com/css2?family=Open+Sans:wght@400;600;700&display=swap" rel="stylesheet">
<style>
  :root {
    --bg: #232323;
    --card-white: #f4f4f4;
    --brand-blue: #1170b8;
    --slate: #8e8f93;
    --slate-light: #b4b5b8;
    --ink: #1c1c1c;
    --rule: #3a3a3a;
    --white: #ffffff;
  }
  * { box-sizing: border-box; margin: 0; padding: 0; }
  html, body { width: 1200px; height: 780px; overflow: hidden; }
  body {
    background: var(--bg);
    font-family: "Open Sans", Arial, sans-serif;
    display: flex;
    align-items: center;
    justify-content: center;
    gap: 40px;
  }
  .card {
    position: relative;
    width: 540px;
    height: 309px;
    overflow: hidden;
    box-shadow: 0 18px 40px rgba(0,0,0,0.55);
  }

  /* Front */
  .card-front { background: var(--card-white); }
  .front-brand {
    position: absolute;
    left: 30px; top: 78px;
    width: 200px;
    display: flex; align-items: center; gap: 10px;
    color: var(--brand-blue);
    font-weight: 700;
    font-size: 25px;
    line-height: 1.1;
  }
  .brand-square {
    flex: 0 0 18px; height: 18px;
    background: var(--brand-blue);
  }
  .front-divider { position: absolute; left: 0; top: 0; }
  .front-details {
    position: absolute;
    left: 300px; top: 44px;
    width: 228px;
    color: var(--ink);
  }
  .person-name { font-size: 26px; font-weight: 700; line-height: 1.1; white-space: nowrap; }
  .person-name .first { color: var(--brand-blue); }
  .person-name .last { color: var(--slate); }
  .person-title { font-size: 14px; font-weight: 600; margin: 2px 0 14px; }
  .contact-list { list-style: none; font-size: 13px; line-height: 1.65; }
  .contact-list li { display: flex; align-items: center; gap: 7px; white-space: nowrap; }
  .contact-list svg { flex: 0 0 12px; }
  .address-band {
    position: absolute;
    left: 0; bottom: 20px;
    width: 430px; height: 30px;
    background: var(--brand-blue);
    color: var(--white);
    font-size: 14px;
    display: flex; align-items: center;
    padding-left: 150px;
    white-space: nowrap;
  }
  .corner-band {
    position: absolute;
    right: 0; bottom: 0;
    width: 110px; height: 70px;
    background: var(--slate-light);
  }

  /* Back */
  .card-back {
    background: linear-gradient(120deg, #85868a 0%, #9a9b9f 55%, #c9cacc 100%);
  }
  .back-pattern { position: absolute; inset: 0; }
  .back-brand {
    position: absolute;
    left: 0; right: 0; top: 50%;
    transform: translateY(-50%);
    text-align: center;
    color: var(--white);
    font-size: 30px;
    font-weight: 700;
  }
</style>
</head>
<body>

  <section class="card card-front" aria-label="Business card front">
    <div class="front-brand"><span class="brand-square"></span>Tall Fern Roofing</div>

    <svg class="front-divider" width="540" height="309" aria-hidden="true">
      <line x1="248" y1="232" x2="284" y2="30" stroke="var(--rule)" stroke-width="1"/>
    </svg>

    <div class="front-details">
      <h1 class="person-name"><span class="first">Dana</span> <span class="last">Whitcomb</span></h1>
      <p class="person-title">Owner</p>
      <ul class="contact-list">
        <li>
          <svg width="12" height="12" viewBox="0 0 12 12" aria-hidden="true"><path d="M3 1 L5 3.5 L4 5 Q5 7 7 8 L8.5 7 L11 9 L9.5 11 Q4 10.5 1 3 Z" fill="var(--brand-blue)"/></svg>
          412-555-0148
        </li>
        <li>
          <svg width="12" height="12" viewBox="0 0 12 12" aria-hidden="true"><circle cx="6" cy="6" r="5" fill="none" stroke="var(--brand-blue)" stroke-width="1.4"/><path d="M1 6 H11 M6 1 Q3 6 6 11 Q9 6 6 1" fill="none" stroke="var(--brand-blue)" stroke-width="1"/></svg>
          www.tallfernroofingllc.com
        </li>
        <li>
          <svg width="12" height="12" viewBox="0 0 12 12" aria-hidden="true"><rect x="1" y="2.5" width="10" height="7" fill="var(--brand-blue)"/><path d="M1 2.5 L6 7 L11 2.5" fill="none" stroke="var(--white)" stroke-width="1"/></svg>
          dana@tallfernroofingllc.com
        </li>
      </ul>
    </div>

    <div class="address-band">PO Box 418 Maple Grove, PA 16050</div>
    <div class="corner-band"></div>
  </section>

  <section class="card card-back" aria-label="Business card back">
    <div class="back-pattern" role="img" aria-label="Repeating rooftop pattern in soft grey tones"></div>
    <p class="back-brand">Tall Fern Roofing</p>
  </section>

</body>
</html>
```